Letterhead for Conveyancing Company

Use existing logo to create a letterhead for a conveyancing company. Must be able to be used in Microsoft Word. Easy to read and professional.
Contact information to be at the bottom.
Bright Oak Conveyancing Pty Ltd
ACN 621 984 736PO Box 535 Campbelltown SA 5074
Mobile - 0461739286
Web address - www.brightoakconveyancing.com.au

Requirements
Must have
• Logo and contact details.
• Simple and professional.

```html
<!DOCTYPE html>
<html lang="en">
<head>
<meta charset="utf-8">
<title>Bright Oak Conveyancing Letterhead</title>
<link href="https://fonts.googleapis.com/css2?family=Arimo:wght@400;700&family=Cormorant+SC:wght@500&display=swap" rel="stylesheet">
<style>
  :root {
    --pink: #e6388f;
    --ink: #6e6e70;
    --backdrop: #dcdfe1;
    --paper: #ffffff;
    --sign-tone: #e9e9ea;
  }
  * { box-sizing: border-box; margin: 0; padding: 0; }
  html, body {
    width: 1200px; height: 784px; overflow: hidden;
    background: var(--backdrop);
  }
  .letterhead {
    position: absolute; left: 330px; top: 10px;
    width: 540px; height: 764px;
    background: var(--paper);
    border-top: 5px solid var(--pink);
    box-shadow: 0 2px 8px rgba(0,0,0,.12);
    font-family: "Arimo", Arial, sans-serif;
  }
  .brand {
    position: absolute; left: 96px; top: 34px;
    display: flex; align-items: center; gap: 8px;
    font-weight: 700; font-size: 30px; line-height: 1;
    color: var(--pink); letter-spacing: -0.5px;
  }
  .brand-dot {
    width: 14px; height: 14px; border-radius: 50%;
    background: var(--pink);
  }
  .contact {
    position: absolute; right: 34px; top: 112px;
    list-style: none; font-size: 6.6px; line-height: 11px; color: var(--ink);
  }
  .contact li { display: flex; align-items: center; gap: 5px; }
  .contact .address { color: var(--pink); font-weight: 700; font-size: 7px; }
  .contact svg { width: 7px; height: 7px; flex: none; }
  .body-copy {
    position: absolute; left: 96px; top: 112px; width: 240px;
    font-size: 8.4px; line-height: 11.6px; color: var(--ink);
  }
  .body-copy p { margin-bottom: 11.6px; }
  .signature {
    position: absolute; left: 96px; top: 560px;
    width: 130px; height: 34px; background: var(--sign-tone);
  }
  .footer-name {
    position: absolute; left: 96px; bottom: 32px;
    font-family: "Cormorant SC", Georgia, serif;
    font-weight: 500; font-size: 15px; letter-spacing: 0.6px;
    color: var(--pink);
  }
</style>
</head>
<body>
<main class="letterhead">
  <div class="brand"><span class="brand-dot"></span>Bright Oak</div>

  <ul class="contact">
    <li class="address">
      <svg viewBox="0 0 10 10"><circle cx="5" cy="5" r="5" fill="#e6388f"/><path d="M5 2.2a1.8 1.8 0 0 0-1.8 1.8C3.2 5.4 5 7.6 5 7.6S6.8 5.4 6.8 4A1.8 1.8 0 0 0 5 2.2z" fill="#fff"/></svg>
      PO Box 871 Marlowdale SA 5096
    </li>
    <li>
      <svg viewBox="0 0 10 10"><circle cx="5" cy="5" r="5" fill="#e6388f"/><rect x="2.6" y="3" width="4.8" height="4" fill="#fff"/></svg>
      ACN 583 217 469
      <svg viewBox="0 0 10 10"><circle cx="5" cy="5" r="5" fill="#e6388f"/><path d="M3.3 2.6l1 1-.6.8c.4.8 1 1.4 1.8 1.8l.8-.6 1 1-.6.9C4.6 7.3 2.7 5.4 2.4 3.2z" fill="#fff"/></svg>
      0461739286
    </li>
    <li>
      <svg viewBox="0 0 10 10"><circle cx="5" cy="5" r="5" fill="#e6388f"/><rect x="2.5" y="3.2" width="5" height="3.6" fill="#fff"/></svg>
      contact@brightoakconveyancing.com.au
    </li>
    <li>
      <svg viewBox="0 0 10 10"><circle cx="5" cy="5" r="5" fill="#e6388f"/><circle cx="5" cy="5" r="2.4" fill="none" stroke="#fff" stroke-width=".8"/></svg>
      www.brightoakconveyancing.com.au
    </li>
  </ul>

  <section class="body-copy">
    <p>Lorem Ipsum is simply dummy text of the printing and typesetting industry. Lorem Ipsum has been the industry's standard dummy text ever since the 1500s, when an unknown printer took a galley of type and scrambled it to make a type specimen book. It has survived not only five centuries, but also the leap into electronic typesetting, remaining essentially unchanged. It was popularised in the 1960s with the release of Typeframe sheets containing Lorem Ipsum passages, and more recently with desktop publishing software like Pagecraft Studio including versions of Lorem Ipsum.</p>
    <p>It is a long established fact that a reader will be distracted by the readable content of a page when looking at its layout. The point of using Lorem Ipsum is that it has a more-or-less normal distribution of letters, as opposed to using 'Content here, content here', making it look like readable English. Many desktop publishing packages and web page editors now use Lorem Ipsum as their default model text, and a search for 'lorem ipsum' will uncover many web sites still in their infancy. Various versions have evolved over the years, sometimes by accident, sometimes on purpose (injected humour and the like).</p>
    <p>Contrary to popular belief, Lorem Ipsum is not simply random text. It has roots in a piece of classical Latin literature from 45 BC, making it over 2000 years old. A Latin professor at a small college looked up one of the more obscure Latin words, consectetur, from a Lorem Ipsum passage, and going through the cites of the word in classical literature, discovered the undoubtable source. Lorem Ipsum comes from sections 1.10.32 and 1.10.33 of "de Finibus Bonorum et Malorum". The generated Lorem Ipsum is therefore always free from repetition, injected humour, or non-characteristic words etc.</p>
  </section>

  <div class="signature" role="img" aria-label="Handwritten signature"></div>

  <div class="footer-name">Bright Oak Conveyancing Pty Ltd</div>
</main>
</body>
</html>
```